Coral Bay Pools New website

I currently operate a swimming pool service and repair business and looking for a re design for my website as it has been over 5 years since it was designed. current site is coralbaypoolslv.com

```html
<!DOCTYPE html>
<html lang="en">
<head>
<meta charset="utf-8">
<title>Coral Bay Pools</title>
<link href="https://fonts.googleapis.com/css2?family=Roboto:wght@400;500;700;900&family=Kaushan+Script&display=swap" rel="stylesheet">
<style>
:root{
  --blue:#1a8fe3;
  --blue-deep:#0d5fb0;
  --orange:#f7931e;
  --navy:#1c3566;
  --dark:#1e2a31;
  --text:#555d66;
  --white:#ffffff;
}
*{box-sizing:border-box;margin:0;padding:0}
html,body{width:1200px;height:4422px;overflow:hidden;background:var(--white);font-family:'Roboto',sans-serif;color:var(--text)}
.page{position:relative;width:1200px;height:4422px;overflow:hidden}
.abs{position:absolute}
.script{font-family:'Kaushan Script',cursive;color:var(--orange);font-size:23px}
.heading{font-family:'Roboto',sans-serif;font-weight:400;color:#1a1a1a;font-size:47px;line-height:1}
.heading b{color:var(--blue);font-weight:700}
.btn{position:absolute;display:flex;align-items:center;justify-content:center;background:var(--orange);color:var(--white);font-weight:700;font-size:13px;border-radius:3px}

/* header */
.header{top:0;left:0;width:1200px;height:100px;background:var(--white)}
.brand{left:103px;top:38px;display:flex;align-items:center;gap:10px;font-weight:700;font-size:24px;color:var(--navy)}
.brand-dot{width:22px;height:22px;border-radius:50%;background:var(--orange)}
.topbar{top:16px;left:410px;display:flex;gap:40px;font-size:15px;color:#222}
.topbar span{display:flex;align-items:center;gap:10px}
.topbar strong{font-weight:700}
.nav{top:55px;left:506px;width:694px;height:45px}
.nav-links{position:absolute;left:0;top:0;display:flex;height:45px;align-items:center;font-size:13px;color:var(--white)}
.nav-links a{color:var(--white);text-decoration:none;padding:0 17px}
.nav-links .active{background:var(--orange);height:45px;display:flex;align-items:center;padding:0 22px 0 36px;clip-path:polygon(22px 0,100% 0,100% 100%,0 100%)}
.nav-cta{position:absolute;left:485px;top:5px;width:96px;height:34px;background:var(--blue);color:var(--white);font-size:13px;font-weight:500;display:flex;align-items:center;justify-content:center;border-radius:2px}

/* hero */
.hero{top:100px;left:0;width:1200px;height:700px;background:linear-gradient(180deg,#3e5b3a 0%,#4d6b45 30%,#2e8fc2 62%,#46b5e6 100%)}
.hero-title{top:298px;left:0;width:1200px;text-align:center;color:var(--white);font-weight:900;font-size:76px;line-height:84px;letter-spacing:-.5px}
.hero-sub{top:486px;left:0;width:1200px;text-align:center;color:var(--white);font-weight:700;font-size:22px}
.hero-book{left:433px;top:542px;width:198px;height:40px}
.hero-est{left:638px;top:542px;width:132px;height:40px;background:var(--white);color:#111}

/* about */
.about-img{left:118px;top:897px;width:440px;height:440px}
.about-eyebrow{left:646px;top:876px}
.about-title{left:646px;top:920px}
.about-text{left:646px;top:978px;width:440px;font-size:13px;line-height:28.4px;text-align:justify}
.about-btn{left:646px;top:1260px;width:114px;height:42px}

/* why */
.why{top:1420px;left:0;width:1200px;height:441px}
.why-photo{left:594px;top:0;width:606px;height:441px;background:linear-gradient(180deg,#cfd3d6 0%,#b4b8ba 45%,#2b9ad4 65%,#1d86c6 100%)}
.why-panel{left:0;top:0;width:594px;height:441px;background:linear-gradient(135deg,#1c8fe0,#2ea4ee);border-radius:0 6px 6px 0}
.why-eyebrow{left:112px;top:62px}
.why-title{left:112px;top:100px;color:var(--white);font-size:47px}
.why-text{left:112px;top:166px;width:410px;color:var(--white);font-size:13.5px;font-weight:500;line-height:31px}
.why-btn{left:110px;top:344px;width:112px;height:40px}

/* services */
.center{left:0;width:1200px;text-align:center}
.svc-eyebrow{top:1940px}
.svc-title{top:1982px}
.svc-sub{top:2044px;font-size:14px}
.card{top:2110px;width:313px;height:350px;background:var(--white);border-radius:4px;box-shadow:0 4px 14px rgba(0,0,0,.18);overflow:hidden}
.card-img{width:313px;height:290px}
.card-label{height:60px;display:flex;align-items:center;justify-content:center;font-size:20px;color:#1a1a1a}

/* contact */
.contact{top:2546px;left:0;width:1200px;height:596px;background:linear-gradient(180deg,#1f4d9a 0%,#163a78 45%,#0f3b73 70%,#1a5a94 100%)}
.contact-eyebrow{top:2588px}
.contact-title{top:2630px;color:var(--white)}
.contact-title b{color:var(--white)}
.field{position:absolute;background:var(--white);border-radius:4px;font-size:14px;color:#777;display:flex;align-items:center;gap:10px;padding:0 16px}
.field svg{flex:none}
.field-area{align-items:flex-start;padding-top:14px}
.contact-btn{left:544px;top:3044px;width:114px;height:41px}

/* gallery */
.gal-eyebrow{top:3213px}
.gal-title{top:3256px}
.g{position:absolute;border-radius:4px}
.g-caption{position:absolute;left:42px;bottom:22px;color:var(--white);font-size:26px;font-weight:500}
.gal-btn{left:544px;top:3808px;width:114px;height:42px}

/* footer */
.footer{top:4060px;left:0;width:1200px;height:362px;background:var(--dark)}
.foot-h{font-size:22px;font-weight:500;color:var(--blue)}
.quick{left:112px;top:4094px}
.quick ul{list-style:none;margin-top:14px}
.quick li{font-size:14px;color:var(--white);line-height:33px;padding-left:4px}
.quick li:first-child{font-weight:700}
.foot-brand{left:0;width:1200px;top:4150px;text-align:center;font-weight:700;font-size:32px;color:var(--white)}
.foot-brand i{display:inline-block;width:20px;height:20px;border-radius:50%;background:var(--orange);margin-right:12px;vertical-align:middle}
.social{left:543px;top:4302px;display:flex;gap:10px}
.social span{width:30px;height:30px;border-radius:50%;background:var(--white)}
.social span:first-child{background:var(--blue)}
.info{left:855px;top:4103px}
.info-row{display:flex;gap:14px;align-items:flex-start;color:var(--white);font-size:14px;line-height:24px;margin-top:18px}
.info-row svg{flex:none;margin-top:3px}
.rule{left:112px;top:4370px;width:976px;height:1px;background:#556069}
.copy{top:4388px;font-size:13px;color:var(--white)}
</style>
</head>
<body>
<div class="page">

  <!-- header -->
  <header class="abs header">
    <div class="abs brand"><span class="brand-dot"></span>Coral Bay Pools</div>
    <div class="abs topbar">
      <span><svg width="24" height="24" viewBox="0 0 24 24"><circle cx="12" cy="12" r="12" fill="#1a8fe3"/><path d="M8 6.5l2 .2 1 3-1.3 1.2c.7 1.5 1.9 2.7 3.4 3.4l1.2-1.3 3 1 .2 2c-.3.8-1 1.3-1.8 1.3C10.8 17.3 6.7 13.2 6.7 8.3c0-.8.5-1.5 1.3-1.8z" fill="#fff"/></svg><strong>Call Us:</strong>(702) 555-0148</span>
      <span><svg width="24" height="24" viewBox="0 0 24 24"><circle cx="12" cy="12" r="12" fill="#1a8fe3"/><rect x="6" y="8" width="12" height="8.5" rx="1" fill="#fff"/><path d="M6.5 8.5l5.5 4 5.5-4" stroke="#1a8fe3" stroke-width="1.3" fill="none"/></svg><strong>Mail Us:</strong>poolsolutions@coralbaypoolslv.com</span>
    </div>
    <nav class="abs nav">
      <svg class="abs" style="left:0;top:0" width="694" height="45"><polygon points="22,0 694,0 694,45 0,45" fill="#1c3566"/></svg>
      <div class="nav-links">
        <a class="active">Home</a>
        <a>About Us</a>
        <a>Our Services</a>
        <a>Free Estimate</a>
      </div>
      <div class="nav-cta">Contact</div>
    </nav>
  </header>

  <!-- hero -->
  <section class="abs hero" role="img" aria-label="Pool technician cleaning a bright blue swimming pool surrounded by ornamental grasses"></section>
  <svg class="abs" style="left:0;top:600px" width="1200" height="200" viewBox="0 0 1200 200">
    <polygon points="0,40 600,172 1200,40 1200,62 600,195 0,62" fill="#f7931e"/>
    <polygon points="0,62 600,195 1200,62 1200,200 0,200" fill="#ffffff"/>
  </svg>
  <h1 class="abs hero-title">Crystal-Clear Pools.<br>Zero Hassle.</h1>
  <p class="abs hero-sub">Nevada’s Best Rated Local Pool Cleaning</p>
  <div class="btn hero-book">Book Your Service Today</div>
  <div class="btn hero-est">Free Estimate</div>

  <!-- about -->
  <svg class="abs about-img" viewBox="0 0 440 440" role="img" aria-label="Pool technician skimming a pool on a sunny lawn">
    <defs><linearGradient id="aboutFill" x1="0" y1="0" x2="0" y2="1"><stop offset="0" stop-color="#3f5b34"/><stop offset=".55" stop-color="#6f9a58"/><stop offset=".75" stop-color="#3aa6e0"/><stop offset="1" stop-color="#1b86cc"/></linearGradient></defs>
    <path d="M220 6 C250 120 320 190 434 220 C320 250 250 320 220 434 C190 320 120 250 6 220 C120 190 190 120 220 6Z" fill="url(#aboutFill)" stroke="#f7931e" stroke-width="4"/>
  </svg>
  <div class="abs script about-eyebrow">Who We Are</div>
  <h2 class="abs heading about-title">About <b>Us</b></h2>
  <p class="abs about-text">When you need professional pool cleaning services in Nevada, you can count on the professionals at Coral Bay Pools to provide you with superior and prompt solutions. Whether you need assistance with a residential or commercial pool, we'll vacuum, brush, and thoroughly clean your pool so it's swim-ready. We'll also clean your pool filters and inform you of any issues that arise. Our staff is certified by the Desert Valley Health District to ensure proper chemical levels and equipment are safe. To learn more about our pool cleaning services or to get your free estimate, contact our pool experts today.</p>
  <div class="btn about-btn">Read &nbsp;More</div>

  <!-- why choose us -->
  <section class="abs why">
    <div class="abs why-photo" role="img" aria-label="Indoor swimming pool with lounge chairs in a modern room"></div>
    <div class="abs why-panel" role="img" aria-label="Blue tinted palm trees behind text"></div>
    <div class="abs script why-eyebrow">Our Benefits</div>
    <h2 class="abs heading why-title">Why Choose Us</h2>
    <p class="abs why-text">Our full-service pool company proudly serves the entire Las Vegas valley, and we’re certified by the Desert Valley Health District to maintain the highest level of pool safety. If you need repairs, maintenance, scheduled cleanings, or any other pool services, contact us online or by phone today.</p>
    <div class="btn why-btn">Contact Us</div>
  </section>

  <!-- services -->
  <div class="abs center script svc-eyebrow">What We Do</div>
  <h2 class="abs center heading svc-title">Our <b>Services</b></h2>
  <p class="abs center svc-sub">When you invested in your pool, you knew it was a long-term investment in both money and time.</p>
  <article class="abs card" style="left:112px">
    <div class="card-img" role="img" aria-label="Pool skimmer net over blue water" style="background:linear-gradient(160deg,#4bb7ef,#1670c4)"></div>
    <div class="card-label">Pool Services</div>
  </article>
  <article class="abs card" style="left:441px">
    <div class="card-img" role="img" aria-label="Technician scrubbing pool tiles with a brush" style="background:linear-gradient(180deg,#8b7a44,#2d7fbf 55%,#1f9ad8)"></div>
    <div class="card-label">Commercial Pool Services</div>
  </article>
  <article class="abs card" style="left:771px">
    <div class="card-img" role="img" aria-label="Technician removing leaves from a residential pool" style="background:linear-gradient(180deg,#b88a38,#5d8a3c 50%,#1e5fa8)"></div>
    <div class="card-label">Residential Pool Services</div>
  </article>

  <!-- contact -->
  <section class="abs contact" role="img" aria-label="Resort pool at dusk lined with palm trees"></section>
  <div class="abs center script contact-eyebrow">Contact Us</div>
  <h2 class="abs center heading contact-title">Let’s <b>Connect With Us</b></h2>
  <div class="field" style="left:117px;top:2714px;width:467px;height:47px"><svg width="14" height="14" viewBox="0 0 14 14"><circle cx="7" cy="4" r="3" fill="#999"/><path d="M1 14c0-4 3-5.5 6-5.5s6 1.5 6 5.5z" fill="#999"/></svg>Name</div>
  <div class="field" style="left:604px;top:2714px;width:471px;height:47px"><svg width="16" height="12" viewBox="0 0 16 12"><rect width="16" height="12" rx="1" fill="#999"/><path d="M1 1l7 5 7-5" stroke="#fff" fill="none"/></svg>Email</div>
  <div class="field" style="left:117px;top:2776px;width:467px;height:47px"><svg width="14" height="14" viewBox="0 0 24 24"><path d="M5 2l4 .3 2 5-2.5 2c1.3 2.8 3.4 4.9 6.2 6.2l2-2.5 5 2 .3 4c-.5 1.5-2 2.5-3.5 2.5C9 21.5 2.5 15 2.5 5.5 2.5 4 3.5 2.5 5 2z" fill="#999"/></svg>Contact Number</div>
  <div class="field" style="left:604px;top:2776px;width:471px;height:47px"><svg width="14" height="14" viewBox="0 0 14 14"><rect x="1" y="1" width="12" height="12" rx="1" fill="#999"/><path d="M4 5h6M4 8h6" stroke="#fff"/></svg>Subject</div>
  <div class="field field-area" style="left:117px;top:2838px;width:958px;height:172px"><svg width="16" height="14" viewBox="0 0 16 14"><path d="M8 1C4 1 1 3.5 1 6.5c0 1.6.9 3 2.3 4L2.5 13l3.3-1.6c.7.2 1.4.3 2.2.3 4 0 7-2.5 7-5.3S12 1 8 1z" fill="#999"/></svg>How can we help you today?*</div>
  <div class="btn contact-btn">Submit Now</div>

  <!-- gallery -->
  <div class="abs center script gal-eyebrow">Projects</div>
  <h2 class="abs center heading gal-title">Our <b>Gallery</b></h2>
  <div class="g" role="img" aria-label="Modern home with illuminated pool at night" style="left:112px;top:3353px;width:443px;height:416px;background:linear-gradient(180deg,#2f4f8c,#4b4a52 55%,#1d2f4e)">
    <div class="g-caption">Lorm Ipsum Dolor Siet</div>
  </div>
  <div class="g" role="img" aria-label="White villa with rectangular pool" style="left:579px;top:3353px;width:220px;height:203px;background:linear-gradient(180deg,#cfe0ee,#7d9a6b 50%,#2a86c6)"></div>
  <div class="g" role="img" aria-label="Infinity pool with umbrellas and ocean view" style="left:810px;top:3353px;width:280px;height:203px;background:linear-gradient(180deg,#2f7fd0,#8cc7ee 45%,#1c8fd6)"></div>
  <div class="g" role="img" aria-label="Lit backyard pool at dusk" style="left:579px;top:3568px;width:280px;height:202px;background:linear-gradient(180deg,#3b5a86,#6b6a72 50%,#2c5c8a)"></div>
  <div class="g" role="img" aria-label="Freeform pool surrounded by trees" style="left:870px;top:3568px;width:220px;height:202px;background:linear-gradient(180deg,#6f9a4e,#6fb2c8 50%,#29a0dc)"></div>
  <div class="btn gal-btn">View All</div>

  <!-- footer -->
  <svg class="abs" style="left:0;top:3910px" width="1200" height="152" viewBox="0 0 1200 152">
    <polygon points="0,134 600,12 1200,134 1200,152 0,152" fill="#f7931e"/>
    <polygon points="0,152 600,28 1200,152" fill="#1e2a31"/>
  </svg>
  <footer class="abs footer"></footer>
  <div class="abs quick">
    <div class="foot-h">Quick Links</div>
    <ul><li>Home</li><li>About Us</li><li>Our Services</li><li>Free Estimate</li><li>Contact Us</li></ul>
  </div>
  <div class="abs foot-brand"><i></i>Coral Bay Pools</div>
  <div class="abs social"><span></span><span></span><span></span></div>
  <div class="abs info">
    <div class="foot-h">Contact Info</div>
    <div class="info-row"><svg width="20" height="20" viewBox="0 0 20 20"><circle cx="10" cy="10" r="10" fill="#fff"/><path d="M10 4a4 4 0 0 0-4 4c0 3 4 8 4 8s4-5 4-8a4 4 0 0 0-4-4z" fill="#1e2a31"/><circle cx="10" cy="8" r="1.5" fill="#fff"/></svg>Lorem Ipsum, USA -437916</div>
    <div class="info-row"><svg width="20" height="20" viewBox="0 0 24 24"><circle cx="12" cy="12" r="12" fill="#fff"/><path d="M8 6.5l2 .2 1 3-1.3 1.2c.7 1.5 1.9 2.7 3.4 3.4l1.2-1.3 3 1 .2 2c-.3.8-1 1.3-1.8 1.3C10.8 17.3 6.7 13.2 6.7 8.3c0-.8.5-1.5 1.3-1.8z" fill="#1e2a31"/></svg>+ (702) 555-0148</div>
    <div class="info-row"><svg width="20" height="20" viewBox="0 0 24 24"><circle cx="12" cy="12" r="12" fill="#fff"/><rect x="6" y="8" width="12" height="8.5" rx="1" fill="#1e2a31"/><path d="M6.5 8.5l5.5 4 5.5-4" stroke="#fff" stroke-width="1.2" fill="none"/></svg>poolsolutions@coralbay<br>poolslv.com</div>
  </div>
  <div class="abs rule"></div>
  <div class="abs center copy">© 2026 Coral Bay Pools .All rights reserved</div>

</div>
</body>
</html>
```